ULMIRA card Technical Architecture

Hello everyone ULMIRA: It is a consulting firm in Architecture and Construction. I require a card duplexing, sober, elegant, classic but not boring. Update 1: Use the following data for the card. Name: Gonzalo Pereda Mauricio Villalta Position: COO Twitter: @ulmiraAT Homepage: ulmira-example.com home address not include the participation of all thank you.

Target Market(s)

Construction companies, Architects and Consulting Engineers

Industry/Entity Type

Consulting

Contact Information for Business Card

Los campos que debe tener:
Nombre, Cargo, email, homepage y twitter

Font styles to use
Serif
Sans Serif
Other font styles liked:
• Me gustan playfair display, open sans y roboto, pero estoy sujeto a sus propuestas

Requirements
Must have
• Colors: Present combined proposals in white, red, gray and black Update 1: The two names must be clearly differentiated from the two surnames
Nice to have
• They are free to present their best proposals. I will bring them immediate feedback to the extent you can go see their designs. Complete data for card and logo files will give the winner the

```html
<!DOCTYPE html>
<html lang="es">
<head>
<meta charset="utf-8">
<title>ULMIRA – Tarjeta de visita</title>
<link rel="stylesheet" href="https://fonts.googleapis.com/css2?family=Open+Sans:wght@400;600&display=swap">
<style>
  :root {
    --stage-top: #a9a9a9;
    --stage-bottom: #8d8d8d;
    --card-light: #ffffff;
    --card-dark: #272727;
    --ink: #2e2e2e;
    --ink-soft: #444444;
    --accent: #c8102e;
    --rule: #9a9a9a;
    --paper-text: #f2f2f2;
  }
  * { box-sizing: border-box; margin: 0; padding: 0; }
  html, body { width: 1200px; height: 900px; overflow: hidden; }
  body {
    position: relative;
    background: linear-gradient(180deg, var(--stage-top), var(--stage-bottom));
    font-family: "Open Sans", Arial, sans-serif;
  }
  .card {
    position: absolute;
    top: 306px;
    width: 440px;
    height: 271px;
    border-radius: 12px;
    box-shadow: 0 1px 3px rgba(0,0,0,0.18);
  }
  .card--front { left: 149px; background: var(--card-light); color: var(--ink); }
  .card--back  { left: 608px; background: var(--card-dark); color: var(--paper-text); }

  /* Front: brand block */
  .brand {
    position: absolute;
    left: 36px;
    top: 32px;
    width: 182px;
    text-align: center;
  }
  .brand__dot {
    display: block;
    width: 30px; height: 30px;
    margin: 0 auto 12px;
    border-radius: 50%;
    background: var(--accent);
  }
  .brand__name {
    font-size: 27px;
    font-weight: 400;
    letter-spacing: 7px;
    line-height: 1;
    color: var(--ink);
    margin-right: -7px;
  }
  .brand__tagline {
    margin-top: 6px;
    padding-top: 3px;
    border-top: 1px solid var(--rule);
    font-size: 8px;
    letter-spacing: 2.2px;
    color: var(--accent);
  }

  /* Front: holder */
  .holder {
    position: absolute;
    right: 29px;
    top: 138px;
    text-align: right;
  }
  .holder__name { font-size: 14px; line-height: 18px; color: var(--accent); }
  .holder__given { font-weight: 600; }
  .holder__family { font-weight: 400; }
  .holder__role { font-size: 11.5px; color: var(--ink-soft); line-height: 15px; }

  .divider {
    position: absolute;
    left: 37px; right: 31px; top: 178px;
    height: 1px;
    background: var(--rule);
  }

  .contacts {
    position: absolute;
    left: 34px;
    top: 183px;
    list-style: none;
    font-size: 12px;
    color: var(--ink-soft);
  }
  .contacts li { display: flex; align-items: center; height: 16px; }
  .contacts svg { width: 9px; height: 9px; margin-right: 8px; flex: none; }

  /* Back */
  .back-brand {
    position: absolute;
    left: 0; right: 0; top: 64px;
    text-align: center;
  }
  .back-brand__dot {
    display: block;
    width: 58px; height: 58px;
    margin: 0 auto 22px;
    border-radius: 50%;
    background: var(--accent);
  }
  .back-brand__name {
    font-size: 40px;
    letter-spacing: 14px;
    line-height: 1;
    margin-right: -14px;
    color: var(--paper-text);
  }
  .back-brand__tagline {
    width: 288px;
    margin: 8px auto 0;
    padding-top: 4px;
    border-top: 1px solid #8a8a8a;
    font-size: 12px;
    letter-spacing: 3px;
    color: var(--paper-text);
  }
</style>
</head>
<body>
  <section class="card card--front" aria-label="Anverso">
    <div class="brand">
      <span class="brand__dot" aria-hidden="true"></span>
      <div class="brand__name">ULMIRA</div>
      <div class="brand__tagline">ARQUITECTURA TÉCNICA</div>
    </div>

    <div class="holder">
      <div class="holder__name"><span class="holder__given">Gonzalo Pereda</span> <span class="holder__family">Mauricio Villalta</span></div>
      <div class="holder__role">COO</div>
    </div>

    <div class="divider"></div>

    <ul class="contacts">
      <li>
        <svg viewBox="0 0 10 10" aria-hidden="true"><rect x="0.5" y="2" width="9" height="6" fill="#c8102e"/><path d="M0.5 2 L5 5.5 L9.5 2" fill="none" stroke="#fff" stroke-width="0.8"/></svg>
        info@ulmira-example.com
      </li>
      <li>
        <svg viewBox="0 0 10 10" aria-hidden="true"><circle cx="5" cy="5" r="4.5" fill="#c8102e"/><path d="M0.5 5 H9.5 M5 0.5 C2.5 3 2.5 7 5 9.5 M5 0.5 C7.5 3 7.5 7 5 9.5" fill="none" stroke="#fff" stroke-width="0.7"/></svg>
        www.ulmira-example.com
      </li>
      <li>
        <svg viewBox="0 0 10 10" aria-hidden="true"><rect x="0.5" y="0.5" width="9" height="9" rx="1.5" fill="#c8102e"/></svg>
        @ulmiraAT
      </li>
    </ul>
  </section>

  <section class="card card--back" aria-label="Reverso">
    <div class="back-brand">
      <span class="back-brand__dot" aria-hidden="true"></span>
      <div class="back-brand__name">ULMIRA</div>
      <div class="back-brand__tagline">ARQUITECTURA TÉCNICA</div>
    </div>
  </section>
</body>
</html>
```